Web Design job: SaaS start-up needs a cutting-edge web design

What's Needed:
- All designs files created
- Fully coded implementation in HTML/CSS/Bootstrap
- Pages: 5 -- see content here http://www.TeamVerdexa.com
-- Home Page
-- The Hidden Value
-- Benefits
-- About us
-- Careers
- The existing site has the textual content for each page. We can tweak to meet specific designs if needed.
- You will need to update/create image and interactive content for pages.

Reference:
Our existing website has a lot of content on it for reference -
http://www.TeamVerdexa.com

Description:
We need a web design that focuses in the UX and conveys the idea of magically fixing company problems by way of using our software.

Home Page
The main goal is to Drive Sales of the SaaS tool. When a visitor lands on our home page they should see: What we do, How we can help their problem and How to contact us.
1. Quickly understand What We Do
-- we sell SaaS software.
-- Need to quickly convey what our software does. It's seems complicated but really its not. See the description in about us for more info and visit our existing site.

2. How we can help their problem
-- We aim to solve any problem related to employees
-- Even if the visitor does not have a specific problem in mind, there are several areas organizations can always improve: (some examples below)
---- Create Stronger, More Productive Teams
---- Build Better Communications Pathways
---- Encourage Innovation and Positive Change
---- Develop and Retain Strong "Company Culture"

3. Be able to Contact Us to get started
-- contacting us to get a sales lead is the ultimate goal.
-- the user should not have to hunt to contact us. needs to be easy.

Other Pages (Hidden Value, Benefit, About Us, Careers):
-- These are informative pages about our software and process.
-- If we grab the attention of the user on the home page then these are the pages that they will explore for more info.
-- Should be able to link to these pages from the main nav or from sections with the homepage. For example: What We Do sections could link to the benefits page. How we help their problem sections could link to the Hidden Value page. Regardless of what links to where, the idea is that we will be able to nav to other areas.

About Us:
Our company name is TeamVerdexa (as in Organizational Analysis). We provide a software as a service (SaaS) that uses a simple 6-question survey to analyze the relationships of people within an Organization and provide leaders with ground-breaking Insights about their teams, interactive social network data visualizations to explore their team's composition and we give detailed profiles of the key players (i.e, who are the Social Bridges, Who are the Knowledge Bottlenecks, Who are the Best Mentors, Who are the people that are completely disconnected/out of the loop). Leaders then use this information to make high level organizational decisions.

What's unique about our software:
-- Powerful analysis results from just a 6-question "pulse-surveys"
-- Innovative Tools for visually exploring the organization through relationships as opposed to org-chart
-- Get real-time results as opposed to waiting months with traditional methods
-- Traditional Org-charts represent the organization's skeleton, whereas we uncover the organization's neural network (how it solves problems).

Preferred fonts (but could be convinced otherwise if looks great):
-- Section titles - Aleo
-- Main body - Lato
-- TeamVerdexa logo - Philosopher

Things we like:
-- We like a big slider as the top of the landing page.

Colors to include:
-- Colors in the logo (red, blue, green, teal) as accent colors

Feel of the site:
-- Cutting-edge Software
-- Professional
-- Social Network flare (we analyze relationships)

Note:
If we find a great match with a designer there is strong possibility to continue the relationship with follow on work redesigning our web-based application.

Target Market(s)

Current customers are Morrow Pike & Fenwell, Clearbrook Valley Bank.
We target anyone that manages a large team. Such as Corporate Leaders, High Level Managers, HR Leaders

Industry/Entity Type

Business Software

Contact Information for Business Card

Logo image
Name of company "TEAMVERDEXA" In Philosopher font.
Tagline: "Unlock the Hidden Value In Your Teams"
Person's Name, Title, email, phone.

Coding

Coded - Design and coding required

Number of Pages Required

4 page

Font styles to use
Other font styles liked:
• Lato, Philosopher, Aero

Colors
ec1f27
0255a3

Requirements
Must have
• See description.
Nice to have
• Things we like:
• We like a big slider as the top of the landing page. Ours is a little clunky and outdated but something fresh and sleek would be great.
• Colors to include:
• We would like to use the colors in the logo as accent colors in the site to give a consistent look and feel.
• Feel of the site:
• Cutting-edge Software
• Professional
• Social Network flare (we analyze relationships)

```html
<!DOCTYPE html>
<html lang="en">
<head>
<meta charset="utf-8">
<title>Careers – TeamVerdexa</title>
<link href="https://fonts.googleapis.com/css2?family=Aleo:wght@400&family=Roboto:wght@300;400&display=swap" rel="stylesheet">
<style>
:root{
  --navy:#001a5c;
  --navy-deep:#00154d;
  --red:#ec1f27;
  --ink:#222;
  --ink-soft:#444;
  --body-grey:#9a9a9a;
  --line:#d9d9d9;
  --white:#fff;
}
*{margin:0;padding:0;box-sizing:border-box}
html,body{width:1074px;height:1200px;overflow:hidden;background:var(--white)}
body{position:relative;font-family:'Roboto',sans-serif;color:var(--ink)}
.site-header{position:absolute;left:0;top:0;width:1074px;height:73px}
.brand{position:absolute;left:80px;top:22px;display:flex;align-items:center;gap:8px;font-family:'Aleo',serif;font-size:20px;color:var(--navy)}
.brand-dot{width:22px;height:22px;border-radius:50%;background:var(--red)}
.main-nav a{position:absolute;top:28px;font-size:13px;color:var(--ink-soft);text-decoration:none;line-height:16px}
.main-nav a.active{top:20px;height:32px;line-height:32px;padding:0 17px;border-radius:16px;background:var(--navy);color:var(--white)}
.page-banner{position:absolute;left:0;top:73px;width:1074px;height:148px;background:linear-gradient(90deg,var(--navy-deep),#0a2470 50%,var(--navy-deep))}
.page-title{position:absolute;left:80px;top:56px;font-family:'Aleo',serif;font-size:30px;font-weight:400;color:var(--white)}
.breadcrumb{position:absolute;right:80px;top:66px;font-size:13px;color:#c9d0e6}
.breadcrumb b{font-weight:400;color:var(--white)}
.hiring{position:absolute;left:0;width:1074px;top:252px;text-align:center;font-family:'Aleo',serif;font-size:30px;font-weight:400}
.openings{position:absolute;left:187px;top:308px;font-family:'Aleo',serif;font-size:20px;font-weight:400}
.job{position:absolute;left:156px;width:762px;height:41px;border:1px solid var(--line);border-radius:21px;font-family:'Aleo',serif;font-size:13px;color:var(--ink-soft);line-height:39px;padding-left:31px}
.job.open{height:42px;border:none;background:var(--navy);color:var(--white);font-size:14px;line-height:42px}
.toggle{position:absolute;right:14px;top:8px;width:25px;height:25px;border-radius:50%;background:var(--navy);color:var(--white);text-align:center;line-height:24px;font-family:'Roboto',sans-serif;font-size:16px}
.job.open .toggle{background:var(--white);color:var(--red);top:9px}
.job-body{position:absolute;left:188px;top:404px;width:706px}
.job-body h3{font-family:'Aleo',serif;font-weight:400;font-size:17px;color:var(--ink-soft);margin-bottom:9px}
.job-body h4{font-family:'Aleo',serif;font-weight:400;font-size:13px;color:var(--ink-soft);margin-bottom:9px}
.job-body p{font-size:13px;line-height:19.2px;color:var(--body-grey);font-weight:300;margin-bottom:24px}
.apply-label{position:absolute;left:158px;top:1050px;font-family:'Aleo',serif;font-size:13px}
.btn{position:absolute;top:1079px;width:123px;height:32px;border-radius:16px;color:var(--white);text-align:center;line-height:32px;font-size:15px;text-decoration:none}
.btn-red{left:156px;background:var(--red)}
.btn-navy{left:284px;background:var(--navy)}
.site-footer{position:absolute;left:0;top:1148px;width:1074px;height:52px;background:var(--navy);color:var(--white);font-size:13px}
.copyright{position:absolute;left:80px;top:18px}
.legal{position:absolute;right:80px;top:20px}
</style>
</head>
<body>
<header class="site-header">
  <div class="brand"><span class="brand-dot"></span>TEAMVERDEXA</div>
  <nav class="main-nav">
    <a href="#" style="left:428px">Home</a>
    <a href="#" style="left:506px">The Hidden Value</a>
    <a href="#" style="left:651px">Benefits</a>
    <a href="#" style="left:742px">About us</a>
    <a href="#" class="active" style="left:821px">Careers</a>
    <a href="#" style="left:926px">Client Login</a>
  </nav>
</header>

<section class="page-banner" role="img" aria-label="Dark blue banner with a faint social network pattern of connected nodes">
  <h1 class="page-title">Careers</h1>
  <div class="breadcrumb"><b>Home</b> &nbsp;|&nbsp; Careers</div>
</section>

<h2 class="hiring">We’re Hiring!</h2>
<h2 class="openings">Current Openings</h2>

<div class="job open" style="top:347px">Sales, System Integration Channel (Major Cities)<span class="toggle">−</span></div>

<div class="job-body">
  <h3>Start-Up Software Company – Sales, System Integration Channel</h3>
  <h4>About the Position</h4>
  <p>TeamVerdexa is looking for a key addition to round out our strong start-up team. This person should understand the challenges of new software and process implementation and adoption. Our platform enables the identification and leverage of key personnel for faster, more effective teams and successful implementations. A preference will be given for candidates with contacts facing this clear business challenge on a daily basis.</p>
  <h4>Compensation</h4>
  <p>We are offering an early stage opportunity to demonstrate the ability to identify prospects, pitch the basic value props and participate in closing customers. An extensive sales background is not essential, but the ability to clearly speak with customers and articulate concise value points is necessary. Initially, compensation will be a generous percentage of revenue generated from targeted customers. Equity will be available for the right person working into our team and demonstrating strong value.</p>
  <h4>About Us</h4>
  <p>TeamVerdexa is the first company to offer a software platform for deep Social Capital analyses and employee profile development, with real-time exploratory capabilities. Our proprietary algorithms help companies optimize the organizational social “topology”, illustrating and improving the ways employees communicate and work together. We have conducted engagements with Fortune 500 companies and have received stellar feedback.</p>
</div>

<div class="job" style="top:837px">Sales, HR Business Intelligence (Major Cities)<span class="toggle">+</span></div>
<div class="job" style="top:886px">Sales, Management Consulting (Major Cities)<span class="toggle">+</span></div>
<div class="job" style="top:936px">UI/UX Designer Intern<span class="toggle">+</span></div>
<div class="job" style="top:986px">Social Network Algorithms Intern<span class="toggle">+</span></div>

<div class="apply-label">Apply online via</div>
<a href="#" class="btn btn-red">Jobvista</a>
<a href="#" class="btn btn-navy">Seedlist</a>

<footer class="site-footer">
  <div class="copyright">© 2016 TeamVerdexa. All Rights Reserved.</div>
  <div class="legal">Terms &amp; Condition &nbsp;|&nbsp; Privacy Policy</div>
</footer>
</body>
</html>
```